Scientific Web Site for KLORVEST

Professional Scientific / Service orientated web site, motto, new logos attached for viewing.

"We measure so the Business Owner can Manage" their environments.
Site needs to be be mobile friendly.

We provide a service to electronically measure cleanliness of any surface and a value added disinfecting fogging surface.

Reports showing locations, trending, tracking and randomized test plans ongoing audits will be made available..

NOTE: Although image of Corona Virus is current we don't wont it plastered through the web site, their is more than the current virus.

Home Page - Professional Scientific / Service Looking
About
Our Approach
Services
Residential
Commercial
Transportation
Gyms
Educational & Daycare
Real Estate - Open for inspections, End of Lease etc

Contact
Mobile #
Email
Form to leave their details

Links to social media, Facebook, Instagram
Reference Sites: Ranked in preference
www.brelmont.com.au
https://www.tidewellhygiene.co.uk/
https://www.mistrova.com/
https://www.zenplax.com.au/specialist-surface-disinfection/
https://www.artfolder.example/design/48172039
https://www.artfolder.example/design/51904476
https://www.artfolder.example/design/47318865

Target Market(s)

Commercial and professional Services

Font styles to use
Sans Serif

Requirements
Must have
• Wix Website
Clean fresh look with appropriate imaging
Web site is a company advertising that will hold static information and we will market through social media.
Nice to have
• Scientific look and feel
Should not have
• Prominent Corona Virus images or references

```html
<!DOCTYPE html>
<html lang="en">
<head>
<meta charset="utf-8">
<title>Klorvest — Surface Hygiene Measurement</title>
<link href="https://fonts.googleapis.com/css2?family=Outfit:wght@300;400;500;600&display=swap" rel="stylesheet">
<style>
:root{
  --orange:#f5821f;
  --ink:#111111;
  --dark:#2b2727;
  --text:#333333;
  --muted:#8a8a8a;
  --light:#f4f4f4;
  --white:#ffffff;
  --field:#1e1e1e;
}
*{box-sizing:border-box;margin:0;padding:0}
html,body{width:1200px;height:5072px;overflow:hidden}
body{font-family:'Outfit',sans-serif;color:var(--text);background:var(--white);position:relative}
.abs{position:absolute}
.ph{position:absolute}

/* header */
.brand{left:140px;top:22px;width:240px;height:82px;display:flex;align-items:center;gap:12px}
.brand-dot{width:16px;height:16px;border-radius:50%;background:var(--orange)}
.brand-name{font-size:36px;font-weight:500;letter-spacing:4px;color:var(--ink)}
.call{left:716px;top:0;width:484px;height:124px;background:var(--orange);color:var(--white);display:flex;align-items:center;justify-content:center;font-size:22px;font-weight:500;letter-spacing:.5px}
.nav{left:0;top:124px;width:1200px;height:66px;background:var(--light);display:flex;align-items:center;padding-left:146px;gap:17px;font-size:11px;text-transform:uppercase;color:var(--ink)}
.nav a{color:inherit;text-decoration:none;padding:6px 0}
.nav a.active{border-bottom:2px solid var(--orange)}

/* buttons */
.btn{position:absolute;display:flex;height:56px;width:205px}
.btn .lbl{flex:1;background:var(--orange);color:var(--white);display:flex;align-items:center;justify-content:center;font-size:17px;font-weight:500;text-transform:uppercase}
.btn .arr{width:52px;background:var(--dark);display:flex;align-items:center;justify-content:center}

/* hero */
.hero-img{left:0;top:190px;width:950px;height:670px;background:linear-gradient(120deg,#c9cdd3,#e8eaee 45%,#9fb1c6)}
.hero-card{left:532px;top:365px;width:613px;height:320px;background:var(--white);box-shadow:0 4px 18px rgba(0,0,0,.08);padding:52px 0 0 48px}
.hero-card h1{font-size:54px;font-weight:500;line-height:66px;color:var(--ink)}

/* services */
.svc{position:absolute;width:286px;height:296px;background:var(--white);box-shadow:0 2px 10px rgba(0,0,0,.1)}
.svc .im{height:235px}
.svc p{text-align:center;font-size:21px;font-weight:500;color:var(--ink);line-height:60px}

/* about */
.about-box{left:144px;top:1757px;width:912px;height:901px;box-shadow:0 2px 12px rgba(0,0,0,.08)}
.about-text{left:144px;top:1757px;width:456px;height:450px;padding:50px 40px}
.about-text h2{font-size:46px;font-weight:500;color:var(--ink);margin-bottom:22px}
.about-text p{font-size:14.5px;line-height:28px;color:var(--muted);font-weight:300}
.quote{left:598px;top:2207px;width:458px;height:451px;padding:78px 0 0 76px}
.quote h2{font-size:46px;font-weight:500;color:var(--ink);line-height:62px}
.quote .or{position:absolute;left:76px;top:340px;font-size:22px;color:var(--ink)}
.quote .or b{font-weight:500;margin-left:8px}

/* testimonials */
.testi-title{left:0;top:2760px;width:1200px;text-align:center;font-size:46px;font-weight:500;color:var(--ink)}
.testi-text{left:195px;top:2868px;width:810px;text-align:center;font-size:15px;line-height:31px;font-style:italic;color:var(--muted);font-weight:300}
.testi-name{left:0;top:3018px;width:1200px;text-align:center;font-size:14px;color:var(--orange);font-weight:500}
.dots{left:578px;top:3086px;display:flex;gap:9px}
.dots i{width:7px;height:7px;border-radius:50%;background:#d8d8d8}
.dots i.on{background:var(--orange)}

/* works */
.works-title{left:144px;top:3172px;width:304px;height:306px;background:var(--white);padding:62px 0 0 78px}
.works-title h2{font-size:50px;font-weight:500;line-height:56px;color:var(--ink)}

/* features */
.feat{position:absolute;top:3885px;height:340px;display:flex;flex-direction:column;align-items:center;padding-top:72px;color:var(--white)}
.feat .ring{width:92px;height:92px;border:3px solid var(--white);border-radius:50%;display:flex;align-items:center;justify-content:center;margin-bottom:40px}
.feat h3{font-size:32px;font-weight:500;line-height:40px;text-align:center}

/* contact */
.contact{left:0;top:4225px;width:1200px;height:847px;background:var(--ink);color:var(--white)}
.contact h2{position:absolute;top:88px;width:1200px;text-align:center;font-size:50px;font-weight:500}
.contact .sub{position:absolute;top:172px;width:1200px;text-align:center;font-size:17px}
.field{position:absolute;left:344px;width:512px;background:var(--field);border:1px solid #2e2e2e;font-size:13px;padding:14px 20px;color:#d8d8d8}
.foot{position:absolute;top:4940px;font-size:14px;line-height:25px;color:#e6e6e6}
.vline{position:absolute;top:4930px;width:1px;height:68px;background:#444}
.soc{position:absolute;top:4955px;width:24px;height:24px;border-radius:50%;background:var(--white)}
</style>
</head>
<body>

<header>
  <div class="abs brand"><span class="brand-dot"></span><span class="brand-name">Klorvest</span></div>
  <div class="abs call">CALL US NOW : 123-456-7890</div>
  <nav class="abs nav">
    <a class="active">Home</a><a>About</a><a>Our Approach</a><a>Services</a><a>Residential</a><a>Commercial</a><a>Transportation</a><a>Gyms</a><a>Educational &amp; Daycare</a><a>Real Estate</a>
  </nav>
</header>

<section>
  <div class="ph hero-img" role="img" aria-label="Gloved hand wiping a desk surface with a pink cloth"></div>
  <div class="abs hero-card"><h1>We measure so the<br>Business Owner<br>can Manage</h1></div>
  <div class="btn" style="left:940px;top:630px"><span class="lbl">Book Now</span><span class="arr"><svg width="14" height="20" viewBox="0 0 14 20"><path d="M3 3l7 7-7 7" fill="none" stroke="#fff" stroke-width="2.5"/></svg></span></div>
</section>

<section>
  <div class="svc" style="left:143px;top:912px"><div class="im" style="background:linear-gradient(135deg,#b65d4a,#e6e6e6)" role="img" aria-label="Technician in protective suit spraying a wall"></div><p>Lorem ipsum</p></div>
  <div class="svc" style="left:457px;top:912px"><div class="im" style="background:linear-gradient(135deg,#e8ecef,#3b7fc4)" role="img" aria-label="Cleaner wiping an office desk"></div><p>Excepteur sin</p></div>
  <div class="svc" style="left:770px;top:912px"><div class="im" style="background:linear-gradient(135deg,#9aa6b1,#e4e8ec)" role="img" aria-label="Technician fogging an office with a backpack sprayer"></div><p>Duis aute irure</p></div>
  <div class="svc" style="left:143px;top:1240px"><div class="im" style="background:linear-gradient(135deg,#cfd6dd,#8796a5)" role="img" aria-label="Technician disinfecting a glass corridor"></div><p>Commodo consequ</p></div>
  <div class="svc" style="left:457px;top:1240px"><div class="im" style="background:linear-gradient(135deg,#444,#d8c83a)" role="img" aria-label="Gloved hands cleaning an oven door"></div><p>Voluptatemccusanti</p></div>
  <div class="svc" style="left:770px;top:1240px"><div class="im" style="background:linear-gradient(135deg,#e3e6ea,#6b5c50)" role="img" aria-label="Cleaner wiping a kitchen counter"></div><p>Quis autem</p></div>
  <div class="btn" style="left:497px;top:1600px"><span class="lbl">Book Now</span><span class="arr"><svg width="14" height="20" viewBox="0 0 14 20"><path d="M3 3l7 7-7 7" fill="none" stroke="#fff" stroke-width="2.5"/></svg></span></div>
</section>

<section>
  <div class="abs about-box"></div>
  <div class="abs about-text">
    <h2>About Us</h2>
    <p>Lorem ipsum dolor sit aonsectetur adipiscing elit, sed do eiusmod tempor incididunt ut labore et dolore magna aliquis ipsum suspendisse ultrices gravidaus commodo viverra maeceaccumsan lacus vel facisum dolor sit aonsectetur adipiscing elit, sed do eiusmod tempor incididunt ut labore et dolor suspendiss incididunt ut labore et dolor suspendisse ultrices gravidae ultrices gravidaus commodo viverra maecea incididunt</p>
  </div>
  <div class="ph" style="left:600px;top:1757px;width:456px;height:450px;background:linear-gradient(135deg,#eef1f3,#b9c3cb)" role="img" aria-label="Technician in protective suit disinfecting a vent"></div>
  <div class="ph" style="left:144px;top:2207px;width:454px;height:451px;background:linear-gradient(135deg,#d6dde3,#2f5a3a)" role="img" aria-label="Worker squeegeeing a window"></div>
  <div class="abs quote">
    <h2>Get a Free<br>Quote Now!</h2>
    <div class="btn" style="left:78px;top:240px"><span class="lbl">Book Now</span><span class="arr"><svg width="14" height="20" viewBox="0 0 14 20"><path d="M3 3l7 7-7 7" fill="none" stroke="#fff" stroke-width="2.5"/></svg></span></div>
    <p class="or">Or Call Us:<b>123-456-7890</b></p>
  </div>
</section>

<section>
  <h2 class="abs testi-title">Testimonials</h2>
  <svg class="abs" style="left:110px;top:2902px" width="36" height="66" viewBox="0 0 36 66"><path d="M32 2L4 33l28 31" fill="none" stroke="#cfcfcf" stroke-width="2"/></svg>
  <svg class="abs" style="left:1054px;top:2902px" width="36" height="66" viewBox="0 0 36 66"><path d="M4 2l28 31L4 64" fill="none" stroke="#cfcfcf" stroke-width="2"/></svg>
  <p class="abs testi-text">Lorem ipsum dolor sit amet, consectetur adipiscing elit, sed do eiusmod tempor incididunt ut labore et dolore magna aliquais ipsum suspendisse ultrices gravidus commodo viverra maecenas accumsan lacus vel facilisis. Lorem ipsum dolor sit amet, consectetur adipiscingsed do eiusmod tempor incididunt ut labore et dolore magna aliquauis ipsum suspendisse ultrices gravida</p>
  <p class="abs testi-name">– MARA T.</p>
  <div class="abs dots"><i></i><i class="on"></i><i></i></div>
</section>

<section>
  <div class="abs works-title"><h2>Our<br>Latest<br>Works</h2></div>
  <div class="ph" style="left:448px;top:3172px;width:304px;height:306px;background:linear-gradient(135deg,#bfc5ca,#eceef0)" role="img" aria-label="Cleaner wiping a washroom basin"></div>
  <div class="ph" style="left:752px;top:3172px;width:304px;height:306px;background:linear-gradient(135deg,#9fb6cc,#e8a0c4)" role="img" aria-label="Gloved hands spraying and wiping a sink"></div>
  <div class="ph" style="left:144px;top:3478px;width:304px;height:307px;background:linear-gradient(135deg,#c8ccd0,#555c63)" role="img" aria-label="Chef cleaning a steel kitchen bench"></div>
  <div class="ph" style="left:448px;top:3478px;width:304px;height:307px;background:linear-gradient(135deg,#d9dde0,#3e7a3a)" role="img" aria-label="Disinfection team in protective suits"></div>
  <div class="ph" style="left:752px;top:3478px;width:304px;height:307px;background:linear-gradient(135deg,#8a6a55,#6fa3d8)" role="img" aria-label="Person polishing a glass table"></div>
</section>

<section>
  <div class="feat" style="left:0;width:400px;background:var(--orange)">
    <div class="ring"><svg width="40" height="40" viewBox="0 0 40 40" fill="none" stroke="#fff" stroke-width="2.5" stroke-linejoin="round"><path d="M6 18h7v16H6zM13 32h16a3 3 0 0 0 3-3l2-10a3 3 0 0 0-3-3h-8l1-6a3 3 0 0 0-6-1l-5 9"/></svg></div>
    <h3>Fully<br>Bonded</h3>
  </div>
  <div class="feat" style="left:400px;width:398px;background:var(--dark)">
    <div class="ring"><svg width="40" height="40" viewBox="0 0 40 40"><path d="M20 5l4.5 9.6 10.5 1.3-7.7 7.2 2 10.4L20 28.3l-9.3 5.2 2-10.4L5 15.9l10.5-1.3z" fill="none" stroke="#fff" stroke-width="2.5" stroke-linejoin="round"/></svg></div>
    <h3>Reliable &amp;<br>Trustworthy</h3>
  </div>
  <div class="feat" style="left:798px;width:402px;background:var(--orange)">
    <div class="ring"><svg width="40" height="40" viewBox="0 0 40 40"><path d="M8 21l8 8 16-17" fill="none" stroke="#fff" stroke-width="5" stroke-linecap="round" stroke-linejoin="round"/></svg></div>
    <h3>Professional &amp;<br>Experienced</h3>
  </div>
</section>

<footer class="abs contact">
  <h2>Contact Us</h2>
  <p class="sub">Call or Message Us for a Free Quote!</p>
  <div class="field" style="top:260px;height:46px">Mobile #</div>
  <div class="field" style="top:320px;height:46px">Email</div>
  <div class="field" style="top:380px;height:116px">Form to leave their details</div>
  <div class="btn" style="left:497px;top:550px"><span class="lbl">Send</span><span class="arr" style="background:#2a2a2a"><svg width="14" height="20" viewBox="0 0 14 20"><path d="M3 3l7 7-7 7" fill="none" stroke="#fff" stroke-width="2.5"/></svg></span></div>
</footer>
<span class="soc" style="left:183px" aria-label="Social media link"></span>
<span class="soc" style="left:223px" aria-label="Social media link"></span>
<span class="vline" style="left:298px"></span>
<p class="foot" style="left:326px">234,Sed ut perspiciatis unmnis<br>istenatus erroruptatem</p>
<span class="vline" style="left:588px"></span>
<p class="foot" style="left:618px">info@companyname.com<br>123-456-7890</p>
<span class="vline" style="left:850px"></span>
<p class="foot" style="left:878px">© 2023 Klorvest<br>All Rights Reserved</p>

</body>
</html>
```